Golden Coat All-Purpose Breading Bag Design

Our client, Halvern Food Products, is looking to re-design the packaging for their product, Pellham's Golden Coat. Goldn Coat is an all-purpose food breading mix.

Halvern Foods has a registered trademark for this product, but they have not been using it for this particular 10 pound bag. They want to get the trademark onto the bag and also give the bag an updated look. They would like to continue to use the same red and blue colors. This 10 pound bag is not available on store shelves; it is sold to food service distributors who sell to restaurants.

All of the copy on the existing bag is still relevant, so we will want to incoprporate it into the bag design. Once these bags are filled with product, the tops get folded over about 1 inch and then sewn shut with thread.

Eventually, we will need the design applied to the Bag Template file attached, but that isn't important until a design is selected.

Target Market(s)

Restaurants

Industry/Entity Type

Food Manufacturing

Colors
0054AA
0677BA
7BADD7
CADEEF
E8F1F8
EB3D1F
EC4F4E
F09395
F8D3D4
FCEDEE

Requirements
Must have
• Trademark introduced to the design

```html
<!DOCTYPE html>
<html lang="en">
<head>
<meta charset="utf-8">
<title>Pellham's Golden Coat – 10 lb Bag</title>
<link rel="stylesheet" href="https://fonts.googleapis.com/css2?family=Montserrat:wght@400;500;600;700;800&display=swap">
<style>
  :root {
    --red: #EB3D1F;
    --red-soft: #EC4F4E;
    --pink: #F8D3D4;
    --pink-light: #FCEDEE;
    --blue-deep: #0054AA;
    --blue: #0677BA;
    --blue-mid: #7BADD7;
    --blue-pale: #CADEEF;
    --blue-light: #E8F1F8;
    --cream: #FBF3EC;
    --ink: #2C3A55;
    --stage: #E9EAEC;
  }
  * { box-sizing: border-box; margin: 0; padding: 0; }
  html, body { width: 1200px; height: 900px; overflow: hidden; }
  body { background: var(--stage); font-family: "Montserrat", sans-serif; color: var(--ink); }
  .bag { position: absolute; left: 30px; top: 60px; width: 1140px; height: 780px; display: flex; }
  .panel { position: relative; height: 100%; }
  .panel::before { content: ""; position: absolute; left: 0; right: 0; top: 0; height: 44px; background: rgba(0,0,0,.05); border-bottom: 1px dashed rgba(0,0,0,.12); }
  .gusset { width: 180px; background: linear-gradient(180deg, var(--pink) 0%, var(--pink-light) 100%); }
  .face { width: 390px; background: var(--blue-pale); }

  /* brand seal */
  .seal { position: absolute; border-radius: 50%; display: flex; flex-direction: column; align-items: center; justify-content: center; text-align: center; color: var(--cream); }
  .seal--main { width: 290px; height: 290px; left: 50px; top: 80px; background: var(--red); }
  .seal--side { width: 130px; height: 130px; left: 25px; top: 110px; background: var(--blue-deep); }
  .seal__name { font-weight: 800; line-height: 1.02; }
  .seal--main .seal__name { font-size: 40px; }
  .seal--side .seal__name { font-size: 17px; }
  .seal__tag { font-weight: 700; letter-spacing: .12em; margin-top: 14px; }
  .seal--main .seal__tag { font-size: 13px; }
  .seal--side .seal__tag { font-size: 6px; margin-top: 8px; }

  /* info boxes */
  .info { position: absolute; left: 22px; right: 22px; border: 2px solid var(--blue-deep); background: var(--blue-light); text-align: center; }
  .info__row { border-bottom: 2px solid var(--blue-deep); padding: 7px 8px; }
  .info__row:last-child { border-bottom: 0; }
  .slogan { font-size: 13px; font-weight: 600; line-height: 1.35; text-transform: uppercase; }
  .slogan .hl-red { color: var(--red); font-weight: 800; }
  .slogan .hl-blue { color: var(--blue-deep); font-weight: 800; }
  .small-caps { font-size: 10px; letter-spacing: .2em; font-weight: 600; text-transform: uppercase; }
  .heading-blue { font-size: 13px; letter-spacing: .14em; font-weight: 700; color: var(--blue-deep); text-transform: uppercase; }
  .body-copy { font-size: 12px; line-height: 1.45; }
  .facts { display: flex; padding: 0; }
  .facts > div { flex: 1; padding: 8px 6px; font-size: 9px; line-height: 1.35; }
  .facts .weight { flex: 0 0 80px; background: var(--blue-deep); color: #fff; font-size: 13px; font-weight: 700; display: flex; flex-direction: column; justify-content: center; }
  .facts .weight small { font-size: 9px; font-weight: 500; }

  .frying { padding: 14px 8px 10px; }
  .frying .for { font-size: 15px; font-weight: 700; color: var(--blue-deep); }
  .frying .big-red { font-size: 30px; font-weight: 800; color: var(--red); line-height: 1.05; }
  .frying .big-blue { font-size: 30px; font-weight: 800; color: var(--blue-deep); line-height: 1.05; }
  .frying .note { font-size: 11px; margin-top: 2px; }

  .side-box { position: absolute; left: 16px; right: 16px; border: 2px solid var(--red); background: var(--pink-light); color: var(--red); text-align: center; padding: 14px 10px; font-size: 11px; line-height: 1.45; font-weight: 500; }
  .side-box p + p { margin-top: 12px; }
  .side-box__row { border-bottom: 2px solid var(--red); margin: 0 -10px; padding: 0 10px 10px; }
  .side-box .kicker { font-size: 8px; letter-spacing: .18em; font-weight: 700; color: var(--blue-deep); }
  .side-box .title { font-size: 16px; letter-spacing: .08em; font-weight: 800; }
  .steps { list-style: none; text-align: left; padding: 12px 0 14px; }
  .steps li { position: relative; padding-left: 14px; margin-bottom: 6px; color: var(--ink); }
  .steps li::before { content: ""; position: absolute; left: 0; top: 5px; width: 6px; height: 6px; border-radius: 50%; background: var(--red); }
  .tip { padding-top: 10px; color: var(--ink); }
</style>
</head>
<body>
<main class="bag" aria-label="Pellham's Golden Coat 10 lb bag, flat panels">

  <!-- left gusset: product story -->
  <section class="panel gusset">
    <div class="seal seal--side">
      <span class="seal__name">Pellham's<br>Golden<br>Coat</span>
      <span class="seal__tag">ALL PURPOSE BREADING</span>
    </div>
    <div class="side-box" style="top:300px;">
      <p>Pellham's Golden Coat is a prepared formula of pure foods that enables you to fry chicken from the raw to the well done in ten minutes. It seals in all the natural juice and creates a very thin crunchy coating which the fat does not penetrate – thereby using much less fat than ordinary frying methods.</p>
      <p>This formula is an all-dry mix to be used on anything breaded – fish, oysters, shrimp, veal and chicken fried steak.</p>
    </div>
  </section>

  <!-- front face -->
  <section class="panel face">
    <div class="seal seal--main">
      <span class="seal__name">Pellham's<br>Golden Coat</span>
      <span class="seal__tag">ALL PURPOSE BREADING</span>
    </div>
    <div class="info" style="top:420px;">
      <div class="info__row slogan">Chicken fried <span class="hl-red">the Golden Coat way</span><br>is the fried chicken <span class="hl-blue">the right way</span></div>
      <div class="info__row small-caps">Seals juice in – grease out</div>
      <div class="info__row">
        <div class="heading-blue">Ingredients</div>
        <div class="body-copy">flour, salt, non fat milk solids, egg yolk, baking powder, corn starch, sugar and pepper</div>
      </div>
      <div class="info__row facts">
        <div>Cooks two pounds chicken well done in 10 minutes (deep fat)</div>
        <div class="weight"><small>Net Wt.</small>10 Lbs</div>
        <div>By Halvern Food Products<br>418 Maple Row<br>Ridgeton, Iowa 50399</div>
      </div>
    </div>
  </section>

  <!-- right gusset: directions -->
  <section class="panel gusset">
    <div class="seal seal--side">
      <span class="seal__name">Pellham's<br>Golden<br>Coat</span>
      <span class="seal__tag">ALL PURPOSE BREADING</span>
    </div>
    <div class="side-box" style="top:300px;">
      <div class="side-box__row">
        <div class="kicker">NOTHING TO ADD</div>
        <div class="title">DIRECTIONS</div>
      </div>
      <ul class="steps side-box__row">
        <li>Wet all foods in water</li>
        <li>Place in dry dip, coating thoroughly</li>
        <li>Deep fry at 350°F for 10 minutes</li>
      </ul>
      <p class="tip">For best results double dip onion rings and oysters</p>
    </div>
  </section>

  <!-- back face -->
  <section class="panel face">
    <div class="seal seal--main">
      <span class="seal__name">Pellham's<br>Golden Coat</span>
      <span class="seal__tag">ALL PURPOSE BREADING</span>
    </div>
    <div class="info" style="top:420px;">
      <div class="info__row frying">
        <div class="for">FOR</div>
        <div class="big-red">DEEP FAT</div>
        <div class="for">AND</div>
        <div class="big-blue">PAN FRYING</div>
        <div class="note">(slightly longer on pan frying)</div>
      </div>
      <div class="info__row">
        <div class="heading-blue">Can be used for</div>
        <div class="body-copy">chicken, steaks, chops, tenderloin, fish, shrimp, oyster and other sea foods, onion rings and vegetables</div>
      </div>
    </div>
  </section>

</main>
</body>
</html>
```